Process Serving Company needs a letterhead design

Looking to have a letterhead designed for letters to attorneys advertising our business. We would like something eye catching but professional. Colors and logos are attached. Please add "Process Service and Attorney Support" near the logo or header

Target Market(s)

Attorneys

Font styles to use
Serif
Sans Serif

Colors
33a6d7
0255a3
85cae6
cee9f5
ecf7fb

```html
<!DOCTYPE html>
<html lang="en">
<head>
<meta charset="utf-8">
<title>Canyon Ridge Letterhead</title>
<link rel="stylesheet" href="https://fonts.googleapis.com/css2?family=Source+Sans+3:wght@400;600&family=Arimo:wght@700&display=swap">
<style>
  :root {
    --sky: #33a6d7;
    --navy: #0255a3;
    --ink: #3a3a3a;
    --greeting: #555555;
    --paper: #ffffff;
    --backdrop: #e6e6e6;
    --sig-fill: #ecf7fb;
  }
  * { margin: 0; padding: 0; box-sizing: border-box; }
  html, body { width: 1059px; height: 1200px; overflow: hidden; background: var(--backdrop); }
  .letterhead {
    position: absolute; left: 104px; top: 0;
    width: 850px; height: 1200px;
    background: var(--paper);
    font-family: "Source Sans 3", sans-serif;
    color: var(--ink);
  }
  .brand {
    position: absolute; left: 174px; top: 58px;
    display: flex; align-items: center; gap: 10px;
  }
  .brand-square { width: 28px; height: 28px; background: var(--sky); }
  .brand-name {
    font-weight: 400; font-size: 30px; letter-spacing: 1px;
    color: var(--sky); line-height: 1;
  }
  .contact {
    position: absolute; left: 641px; top: 45px;
    list-style: none; font-size: 13px; line-height: 17px; color: var(--ink);
  }
  .contact li { display: flex; align-items: center; gap: 6px; }
  .contact svg { width: 10px; height: 10px; fill: var(--sky); flex: none; }
  .greeting {
    position: absolute; left: 70px; top: 266px;
    font-family: "Arimo", sans-serif; font-weight: 700; font-size: 18px;
    color: var(--greeting);
  }
  .letter-body {
    position: absolute; left: 71px; top: 324px; width: 711px;
    font-size: 15.5px; line-height: 22px; text-align: justify;
    text-align-last: left;
  }
  .letter-body p + p { margin-top: 22px; }
  .signature {
    position: absolute; left: 70px; top: 750px;
    width: 117px; height: 56px; background: var(--sig-fill); border-radius: 4px;
  }
  .footer-band { position: absolute; left: 0; bottom: 0; width: 850px; height: 30px; }
  .footer-address {
    position: absolute; left: 0; bottom: 6px; width: 850px; text-align: center;
    font-size: 13px; font-weight: 600; color: var(--paper);
  }
</style>
</head>
<body>
<main class="letterhead">
  <header>
    <div class="brand">
      <span class="brand-square"></span>
      <span class="brand-name">CANYON RIDGE</span>
    </div>
    <ul class="contact">
      <li><svg viewBox="0 0 10 10"><path d="M2 0 L4 2.5 L3 3.6 Q4.5 6 6.4 7 L7.5 6 L10 8 L8.5 10 Q3 9 0 1.5 Z"/></svg>555-014-2020</li>
      <li><svg viewBox="0 0 10 10"><rect x="2" y="0" width="6" height="3"/><rect x="0" y="3.5" width="10" height="4.5" rx="1"/><rect x="2" y="8" width="6" height="2"/></svg>555-014-2020</li>
      <li><svg viewBox="0 0 10 10"><rect x="0" y="2" width="10" height="6.5"/><path d="M0 2 L5 6 L10 2" stroke="#fff" stroke-width="1" fill="none"/></svg>info@canyonridgeserve.com</li>
      <li><svg viewBox="0 0 10 10"><circle cx="5" cy="5" r="4.5"/><path d="M0.5 5 H9.5 M5 0.5 V9.5" stroke="#fff" stroke-width="0.8"/></svg>www.canyonridgeserve.com</li>
    </ul>
  </header>

  <h1 class="greeting">Dear Mr. Carter,</h1>

  <section class="letter-body">
    <p>Lorem Ipsum is simply dummy text of the printing and typesetting industry. Lorem Ipsum has been the industry's standard dummy text ever since the 1500s, when an unknown printer took a galley of type and scrambled it to make a type specimen book. It has survived not only five centuries, but also the leap into electronic typesetting, remaining essentially unchanged.</p>
    <p>The standard chunk of Lorem Ipsum used since the 1500s is reproduced below for those interested. Sections 1.10.32 and 1.10.33 from "de Finibus Bonorum et Malorum" by Varro Lentulus are also reproduced in their exact original form, accompanied by English versions from the 1914 translation by H. Ashcombe</p>
    <p>Lorem Ipsum is simply dummy text of the printing and typesetting industry. Lorem Ipsum has been the industry's standard dummy text ever since the 1500s, when an unknown printer took a galley of type and scrambled it to make a type specimen book. It has survived not only five centuries, but also the leap into electronic typesetting, remaining essentially unchanged. It was popularised in the</p>
    <p>Lorem Ipsum is simply dummy text of the printing and typesetting industry. Lorem Ipsum has been the industry's standard dummy text ever since the 1500s, when an unknown printer took a galley of type and scrambled it to make a type specimen book.</p>
  </section>

  <div class="signature" role="img" aria-label="Handwritten signature of the sender"></div>

  <footer>
    <svg class="footer-band" viewBox="0 0 850 30" preserveAspectRatio="none">
      <rect x="0" y="2" width="850" height="7" fill="var(--sky)"/>
      <rect x="0" y="18" width="850" height="12" fill="var(--navy)"/>
      <path d="M160 30 Q160 9 180 0 H673 Q692 9 692 30 Z" fill="#ffffff"/>
      <path d="M167 30 Q167 11 186 2 H666 Q685 11 685 30 Z" fill="var(--navy)"/>
    </svg>
    <p class="footer-address">4120 E Mesquite Ave #210 Tempe AZ 85281</p>
  </footer>
</main>
</body>
</html>
```